Innovative cost reduction consultant needs to build a group of technical advisors

We need to share our message and compassion for developing cost reduction in the automotive industry. We create opportunities for immediate innovation, by developing cost reduction solutions across suppliers with related process. Attached is an existing Power Point, but it needs improvement. Most of all, a good compelling story, why experts should join us.

Target Market(s)

Automotive industry, supply chain management

Industry/Entity Type

Automotive

Font styles to use
Serif
Sans Serif

Requirements
Must have
• Better visual graphics. There are a few, but they are not as visually appearing as I would like. A graphic with data should have a better visual impact then the ones that I created. I would like to share the message, that I am providing a solution for the automotive industry. The goal is to reduce costs and improve supplier and OEM relationships. The objective is to do so by creating opportunities for immediate innovation, by developing cost reduction solutions across suppliers with related processes. This message may need a visual graphic, which is missing from the presentation.
Nice to have
• Challenge my story and presentation. Does this make sense to you, and what is your opinions of the subject. Or, a relevant news source to validate the story.
Should not have
• I have not decided on the name of the venture or logo. So, let's just use my name as the source or writer. Marcus Delby, Cost Reduction Specialist. Thanks,

```html
<!DOCTYPE html>
<html lang="en">
<head>
<meta charset="utf-8">
<title>Marcus Delby – Cost Reduction Specialist</title>
<link rel="stylesheet" href="https://fonts.googleapis.com/css2?family=EB+Garamond:wght@400;500&family=Roboto+Condensed:wght@300;400;700&family=Roboto:wght@900&family=Michroma&display=swap">
<style>
  :root {
    --stage: #e6ebf2;
    --white: #ffffff;
    --ink: #1a1a1a;
    --ink-soft: #555555;
    --band: #29abe2;
    --navy: #0b5cab;
    --sky: #35a8dc;
    --label: #1763b3;
    --body-text: #555a60;
    --photo-deep: #1f3f7a;
    --photo-mid: #4f77b0;
    --photo-light: #b9cfe6;
  }
  * { box-sizing: border-box; margin: 0; padding: 0; }
  html, body { width: 1200px; height: 1200px; overflow: hidden; }
  body { background: var(--stage); position: relative; font-family: "Roboto Condensed", sans-serif; }

  .slide {
    position: absolute; left: 120px; width: 960px; height: 520px;
    overflow: hidden; box-shadow: 0 2px 8px rgba(0,0,0,0.18);
  }
  .slide--title { top: 66px; background: var(--white); }
  .slide--strength { top: 614px; }
  .slide__band { position: absolute; left: 0; right: 0; bottom: 0; height: 21px; background: var(--band); }

  /* Title slide */
  .brand { position: absolute; left: 0; right: 0; top: 300px; text-align: center; }
  .brand__name { font-family: "EB Garamond", serif; font-weight: 500; font-size: 62px; line-height: 1; color: var(--ink); }
  .brand__tagline { font-family: "EB Garamond", serif; font-size: 17px; letter-spacing: 5.5px; color: var(--ink-soft); margin-top: 4px; padding-left: 60px; }

  /* Strength slide */
  .photo {
    position: absolute; inset: 0;
    background: linear-gradient(100deg, var(--photo-mid) 0%, var(--photo-light) 35%, var(--photo-mid) 60%, var(--photo-deep) 80%, var(--photo-light) 100%);
  }
  .tech-label { position: absolute; left: 49px; font-family: "Michroma", sans-serif; font-size: 11px; letter-spacing: 4px; color: rgba(255,255,255,0.8); }
  .tech-label--top { top: 48px; }
  .tech-label--bottom { top: 484px; left: 26px; }
  .slide__title {
    position: absolute; left: 62px; top: 58px; font-family: "Roboto", sans-serif; font-weight: 900;
    font-size: 62px; line-height: 1; color: var(--white); text-shadow: 0 2px 4px rgba(0,0,0,0.35); letter-spacing: -1px;
  }
  .panel { position: absolute; left: 0; top: 132px; width: 438px; height: 312px; background: var(--white); border-radius: 0 8px 8px 0; }
  .effort-label { position: absolute; font-size: 17px; color: var(--label); }
  .effort-label--small { left: 88px; top: 47px; }
  .effort-label--large { left: 292px; top: 6px; }
  .effort-box { position: absolute; display: flex; align-items: center; justify-content: center; color: var(--white); font-weight: 700; border-radius: 6px; }
  .effort-box--small { left: 81px; top: 71px; width: 87px; height: 47px; background: var(--navy); font-size: 25px; }
  .effort-box--large { left: 247px; top: 31px; width: 158px; height: 86px; background: var(--sky); font-size: 36px; }
  .balance { position: absolute; left: 78px; top: 120px; }
  .base-label { position: absolute; left: 160px; top: 153px; width: 150px; text-align: center; font-size: 17px; color: var(--label); }
  .point { position: absolute; left: 66px; top: 188px; width: 352px; display: flex; gap: 8px; }
  .point__text { font-weight: 300; font-size: 19px; letter-spacing: -0.3px; line-height: 24px; color: var(--body-text); text-align: justify; }
  .point svg { flex: none; margin-top: 6px; }

  .mini-brand { position: absolute; left: 790px; top: 438px; width: 108px; height: 82px; background: var(--white); border-radius: 4px 4px 0 0; text-align: center; padding-top: 46px; }
  .mini-brand__name { font-family: "EB Garamond", serif; font-weight: 500; font-size: 15px; line-height: 1; color: var(--ink); }
  .mini-brand__tagline { font-family: "EB Garamond", serif; font-size: 5px; letter-spacing: 0.8px; color: var(--ink-soft); margin-top: 2px; }
</style>
</head>
<body>

<section class="slide slide--title">
  <div class="brand">
    <div class="brand__name">Marcus Delby</div>
    <div class="brand__tagline">Cost Reduction Specialist</div>
  </div>
  <div class="slide__band"></div>
</section>

<section class="slide slide--strength">
  <div class="photo" role="img" aria-label="Businessman in a dark suit and blue tie pointing at a glowing digital interface with world map and data panels"></div>
  <div class="tech-label tech-label--top">NETWORK SEARCH</div>
  <h1 class="slide__title">Strength</h1>

  <div class="panel">
    <div class="effort-label effort-label--large">Max Effort</div>
    <div class="effort-label effort-label--small">Max Effort</div>
    <div class="effort-box effort-box--small">$23M</div>
    <div class="effort-box effort-box--large">$96M</div>
    <svg class="balance" width="332" height="34" viewBox="0 0 332 34">
      <rect x="2" y="3" width="326" height="3" fill="#0b5cab"/>
      <polygon points="156,6 128,31 184,31" fill="#0b5cab"/>
    </svg>
    <div class="base-label">$3B supplier base</div>
    <div class="point">
      <svg width="9" height="14" viewBox="0 0 9 14"><polygon points="0,0 9,7 0,14" fill="#29abe2"/></svg>
      <p class="point__text">Managing cost is more than mere price reduction. It is a longer term strategy and requires a more collaborative effort towards cost reduction.</p>
    </div>
  </div>

  <div class="tech-label tech-label--bottom">NETWORK SEARCH</div>
  <div class="slide__band"></div>
  <div class="mini-brand">
    <div class="mini-brand__name">Marcus Delby</div>
    <div class="mini-brand__tagline">Cost Reduction Specialist</div>
  </div>
</section>

</body>
</html>
```